Law Firm Logo and Business Card Design

I need a logo and business card design for a law firm I just started. The law firm is named Law Office of Doreen K. Ashworth, LLC. The type of law I practice is Family Law, which includes divorce, custody, child support, alimony, property division, and the like. I would like to see designs that are unique and modern, yet sophisticated. I would also like to use the logo/design for my letterhead. I am not opposed to using some form of the scales of justice although I'd like something other than the typical, old fashioned scales of justice. I had considered a house made out of puzzle pieces with one puzzle piece pulled away from the others, with the logo text reading "Helping your family move forward, one step at a time." However, I don't want that particular design to look juvenile. I also would not be opposed to some form of my initials on the logo -- my initials are DKA. I am open to any other ideas you may have. I would like to see raised designs/lettering, and/or metallic finish. I like the colors black, white, gold, silver, and/or teal.

Industry/Entity Type

Law Firm

```html
<!DOCTYPE html>
<html lang="en">
<head>
<meta charset="utf-8">
<title>Law Office of Doreen K. Ashworth, LLC — Business Card</title>
<link rel="stylesheet" href="https://fonts.googleapis.com/css2?family=Noto+Sans:wght@700&family=Roboto+Condensed:wght@400&display=swap">
<style>
  :root {
    --page: #ffffff;
    --frame: #1c1c1b;
    --card: #d9d9d9;
    --teal: #1f6f78;
    --orange: #e8821c;
    --band: #1c1c1b;
    --ink: #1c1c1b;
  }
  html, body {
    margin: 0;
    padding: 0;
    overflow: hidden;
    background: var(--page);
  }
  .canvas {
    position: relative;
    width: 1200px;
    height: 751px;
    box-sizing: border-box;
    border: 2px solid var(--frame);
    background: var(--page);
    overflow: hidden;
  }
  .card {
    position: absolute;
    left: 60px;
    top: 64px;
    width: 1075px;
    height: 618px;
    background: var(--card);
    overflow: hidden;
  }
  .brand-mark {
    position: absolute;
    left: 684px;
    top: 89px;
    width: 300px;
    height: 64px;
    display: flex;
    align-items: center;
    justify-content: center;
    gap: 16px;
  }
  .brand-dot {
    width: 34px;
    height: 34px;
    border-radius: 50%;
    background: var(--teal);
  }
  .brand-name {
    font-family: "Noto Sans", sans-serif;
    font-weight: 700;
    font-size: 64px;
    line-height: 1;
    color: var(--teal);
    letter-spacing: 2px;
  }
  .tagline {
    position: absolute;
    left: 614px;
    top: 214px;
    width: 440px;
    margin: 0;
    text-align: center;
    font-family: "Roboto Condensed", sans-serif;
    font-weight: 400;
    font-size: 19px;
    line-height: 22px;
    color: var(--ink);
    white-space: nowrap;
  }
  .firm-name {
    position: absolute;
    left: 155px;
    top: 374px;
    margin: 0;
    font-family: "Noto Sans", sans-serif;
    font-weight: 700;
    font-size: 53px;
    line-height: 64px;
    color: var(--teal);
    white-space: nowrap;
  }
  .accent-rule {
    position: absolute;
    left: 0;
    top: 524px;
    width: 100%;
    height: 4px;
    background: var(--orange);
  }
  .footer-band {
    position: absolute;
    left: 0;
    top: 532px;
    width: 100%;
    height: 86px;
    background: var(--band);
  }
</style>
</head>
<body>
  <main class="canvas">
    <section class="card">
      <div class="brand-mark">
        <span class="brand-dot"></span>
        <span class="brand-name">DKA</span>
      </div>
      <p class="tagline">"Helping your family move forward, one step at a time."</p>
      <h1 class="firm-name">Law Office of<br>Doreen K. Ashworth, LLC.</h1>
      <div class="accent-rule"></div>
      <div class="footer-band"></div>
    </section>
  </main>
</body>
</html>
```